Business Card Design

I already have a company logo for my company. I have a logo for the manufacturer we represent. I want a professional business card design.

```html
<!DOCTYPE html>
<html lang="en">
<head>
<meta charset="utf-8">
<title>Beacon Alert Systems — Business Card</title>
<link rel="stylesheet" href="https://fonts.googleapis.com/css2?family=Montserrat:wght@700;800&family=Open+Sans:wght@400;600&display=swap">
<style>
  :root {
    --backdrop: #2a2a2e;
    --card: #ffffff;
    --red: #e3262d;
    --gold: #b8922e;
    --ink: #1c1c1c;
  }
  * { box-sizing: border-box; margin: 0; padding: 0; }
  html, body {
    width: 1200px; height: 780px; overflow: hidden;
    background: var(--backdrop);
  }
  .stage {
    width: 1200px; height: 780px;
    display: flex; align-items: center; justify-content: center; gap: 40px;
  }
  .card {
    position: relative;
    width: 540px; height: 309px;
    background: var(--card);
    box-shadow: 0 14px 30px rgba(0,0,0,0.45);
    overflow: hidden;
  }
  .edge-bar {
    position: absolute; width: 13px; background: var(--red);
  }
  .edge-bar--left { left: 0; top: 24%; height: 53%; }
  .edge-bar--right { right: 0; top: 20%; height: 53%; }

  .brand {
    position: absolute;
    display: flex; align-items: center; gap: 10px;
  }
  .brand__dot {
    width: 30px; height: 30px; border-radius: 50%; background: var(--red); flex: none;
  }
  .brand__name {
    font-family: "Montserrat", sans-serif; font-weight: 800;
    color: var(--red); text-transform: uppercase; line-height: 1.05;
    letter-spacing: 0.5px;
  }
  .card--front .brand { left: 50%; top: 50%; transform: translate(-50%, -50%); }
  .card--front .brand__name { font-size: 28px; }
  .card--front .brand__dot { width: 40px; height: 40px; }

  .card--back .brand { left: 40px; top: 50%; transform: translateY(-60%); }
  .card--back .brand__name { font-size: 20px; }

  .divider {
    position: absolute; left: 265px; top: 52px; width: 1px; height: 155px;
    background: var(--gold);
  }
  .contact { position: absolute; left: 290px; top: 52px; }
  .contact__name {
    font-family: "Montserrat", sans-serif; font-weight: 800; font-size: 25px;
    line-height: 1; white-space: nowrap;
  }
  .contact__first { color: var(--red); }
  .contact__last { color: var(--gold); }
  .contact__title {
    font-family: "Open Sans", sans-serif; font-weight: 600; font-size: 12.5px;
    color: var(--ink); margin-top: 6px;
  }
  .contact__list { list-style: none; margin-top: 22px; }
  .contact__item {
    display: flex; align-items: center; gap: 8px;
    font-family: "Open Sans", sans-serif; font-size: 12.5px; color: var(--ink);
    margin-bottom: 5px;
  }
  .contact__icon { width: 14px; height: 14px; flex: none; }
  .address {
    position: absolute; right: 40px; bottom: 34px;
    font-family: "Open Sans", sans-serif; font-size: 13.5px; color: var(--ink);
    letter-spacing: 0.2px;
  }
</style>
</head>
<body>
<main class="stage">
  <section class="card card--front" aria-label="Card front">
    <span class="edge-bar edge-bar--left"></span>
    <span class="edge-bar edge-bar--right"></span>
    <div class="brand">
      <span class="brand__dot"></span>
      <span class="brand__name">Beacon Alert<br>Systems</span>
    </div>
  </section>

  <section class="card card--back" aria-label="Card back">
    <span class="edge-bar edge-bar--left"></span>
    <span class="edge-bar edge-bar--right"></span>
    <div class="brand">
      <span class="brand__dot"></span>
      <span class="brand__name">Beacon Alert<br>Systems</span>
    </div>
    <span class="divider"></span>
    <div class="contact">
      <p class="contact__name"><span class="contact__first">Daniel</span> <span class="contact__last">Corvin</span></p>
      <p class="contact__title">Managing Director</p>
      <ul class="contact__list">
        <li class="contact__item">
          <svg class="contact__icon" viewBox="0 0 24 24" aria-hidden="true"><circle cx="12" cy="12" r="12" fill="#e3262d"/><path d="M8.5 6.5l2 2-1.2 1.6a7 7 0 0 0 4.6 4.6l1.6-1.2 2 2-1.3 1.8c-4.6-.3-8.3-4-8.6-8.6z" fill="#fff"/></svg>
          <span>(555) 014-2738</span>
        </li>
        <li class="contact__item">
          <svg class="contact__icon" viewBox="0 0 24 24" aria-hidden="true"><circle cx="12" cy="12" r="12" fill="#e3262d"/><rect x="6" y="8" width="12" height="8.5" fill="#fff"/><path d="M6 8l6 5 6-5" fill="none" stroke="#e3262d" stroke-width="1.3"/></svg>
          <span>info@beaconalert.com</span>
        </li>
        <li class="contact__item">
          <svg class="contact__icon" viewBox="0 0 24 24" aria-hidden="true"><circle cx="12" cy="12" r="12" fill="#e3262d"/><circle cx="12" cy="12" r="6" fill="none" stroke="#fff" stroke-width="1.4"/><path d="M6 12h12M12 6c-2.5 3-2.5 9 0 12M12 6c2.5 3 2.5 9 0 12" fill="none" stroke="#fff" stroke-width="1.2"/></svg>
          <span>www.beaconalert.com</span>
        </li>
      </ul>
    </div>
    <p class="address">412 Harlow Ave Fairview, Texas 75000 USA</p>
  </section>
</main>
</body>
</html>
```